NZ First of it's kind solutions directory and marketplace for busy Mums needs a business card design

We need a business card design for our new nationwide business in NZ (long term plans to go global). We provide solutions to the everyday challenges that busy Mums face by connecting them with quality communities and suppliers of carefully selected, relevant products and services. We sell direct via our online marketplace. The final design should communicate our values of inclusivity, quality and smart solutions. Colours should incorporate our logo colour palette of #477077 and #6ba8b2. Our website is at https://www.brightnestmums.example

Target Market(s)

busy Mums, Age 28 – 50, female, income over $100K, location main centres NZ primarily but NZ wide. Is likely juggling work or career with a young family. Probably had hobbies which have fallen by the wayside.
-Wants to succeed in her chosen career without compromising on family life
-to successfully juggle her career without feeling like she is compromising her children
- Is time poor, something always has to give and it’s generally her health (she’ll stay up late, get stressed)
- probably ex corporate or professional career. Has discretional income

Industry/Entity Type

Business

Contact Information for Business Card

Lena Forbisher, Founder, BrightNestMums.example (Strapline Tap; Gather; Sorted), 47 Kowhai Terrace, Ellerslie, Auckland 1051, New Zealand. Mob: 021 483 517 Ph: +64 (0)9 571 4860

Font styles to use
Other font styles liked:
• Raleway, and/or Architects Daughter

Colors
00a990
33b8a4
86cfc6
cfeae6

Requirements
Must have
• the above details, streamline. the logo and colours associated with those logos
Should not have
• foil or metallic colours

```html
<!DOCTYPE html>
<html lang="en">
<head>
<meta charset="utf-8">
<title>BrightNestMums — Business Card</title>
<link rel="stylesheet" href="https://fonts.googleapis.com/css2?family=Work+Sans:wght@400;500;600&display=swap">
<style>
  :root {
    --brand-dark: #477077;
    --brand-light: #6ba8b2;
    --page-bg: #e0e0e0;
    --card-white: #ffffff;
    --text-on-photo: #ffffff;
  }
  * { box-sizing: border-box; margin: 0; padding: 0; }
  html, body {
    width: 1200px; height: 897px; overflow: hidden;
    background: var(--page-bg);
    font-family: "Work Sans", Arial, sans-serif;
  }
  .canvas { position: relative; width: 1200px; height: 897px; }

  .card {
    position: absolute; left: 303px; width: 595px; height: 339px;
    overflow: hidden;
  }
  .card--front { top: 92px; background: var(--card-white); }
  .card--back { top: 469px; }

  .brand {
    position: absolute; display: flex; align-items: center; gap: 12px;
    font-weight: 600; letter-spacing: -0.5px; white-space: nowrap;
  }
  .brand__dot { width: 26px; height: 26px; border-radius: 50%; flex: none; }
  .card--front .brand { top: 50px; right: 28px; font-size: 31px; color: var(--brand-dark); }
  .card--front .brand__dot { background: var(--brand-dark); }

  .holder { position: absolute; left: 32px; top: 180px; }
  .holder__name { font-size: 29px; font-weight: 500; color: var(--brand-light); line-height: 1; }
  .holder__role { font-size: 15px; color: var(--brand-dark); margin-top: 4px; letter-spacing: 0.5px; }

  .divider {
    position: absolute; left: 32px; right: 28px; top: 247px;
    border-top: 1.5px solid var(--brand-dark);
  }
  .contact {
    position: absolute; left: 32px; top: 268px;
    font-size: 13px; line-height: 22px; color: var(--brand-dark);
    letter-spacing: 0.5px; white-space: nowrap;
  }
  .contact__label { color: var(--brand-light); }

  .card__photo {
    position: absolute; inset: 0;
    background:
      radial-gradient(ellipse at 75% 40%, rgba(200,150,90,0.55), transparent 55%),
      radial-gradient(ellipse at 40% 20%, #7a4a2c, transparent 50%),
      linear-gradient(180deg, #6c5a4c 0%, #8a7a6c 55%, #5c5a5a 100%);
  }
  .card--back .brand {
    top: 150px; left: 50%; transform: translateX(-50%);
    font-size: 40px; color: var(--text-on-photo);
  }
  .card--back .brand__dot { background: var(--text-on-photo); width: 32px; height: 32px; }
  .back__url {
    position: absolute; left: 0; right: 0; top: 290px; text-align: center;
    font-size: 15px; letter-spacing: 1px; color: var(--text-on-photo);
  }
</style>
</head>
<body>
<main class="canvas">
  <section class="card card--front">
    <div class="brand"><span class="brand__dot"></span>BrightNestMums</div>
    <div class="holder">
      <h1 class="holder__name">Lena Forbisher</h1>
      <p class="holder__role">Founder</p>
    </div>
    <div class="divider"></div>
    <address class="contact" style="font-style:normal">
      <div><span class="contact__label">M :</span> 021 483 517 | <span class="contact__label">P :</span> +64 (0)9 571 4860 | <span class="contact__label">W :</span> www.brightnestmums.example</div>
      <div><span class="contact__label">A :</span> 47 Kowhai Terrace, Ellerslie Auckland 1051, New Zealand</div>
    </address>
  </section>

  <section class="card card--back">
    <div class="card__photo" role="img" aria-label="Photo of a tired mother resting her face against her hands, in warm soft tones"></div>
    <div class="brand"><span class="brand__dot"></span>BrightNestMums</div>
    <p class="back__url">www.brightnestmums.example</p>
  </section>
</main>
</body>
</html>
```